A private security company called "Tavron Security Services Ltd"

Hello everybody,

We need a web page for a company based in NZ. It is mainly an informative website so it would be wonderful if the designer puts their absolute best into making it a website that I would really appreciate. The website needs to show professionalism and also needs to make our web surfers find the information they need in a click. the company's colour is black and silver, and if those two colours could be integrated into the website it would be absolutely lovely. Please do contact me for any information.

Sincerely,
Dorian Vaskel

Industry/Entity Type

Security

```html
<!DOCTYPE html>
<html lang="en">
<head>
<meta charset="utf-8">
<title>Tavron Security Services Ltd</title>
<link rel="stylesheet" href="https://fonts.googleapis.com/css2?family=Montserrat:wght@400;600&family=Open+Sans:wght@400;600;700&family=Source+Sans+3:wght@300;700&display=swap">
<style>
:root{
  --ink:#111;
  --text:#555;
  --line:#d6d6d6;
  --band:#e9eaec;
  --black:#0d0d0d;
  --footer:#2d2d2d;
  --footer-deep:#1b1b1b;
  --silver:#c9ccd0;
  --cream:#f6efe1;
  --white:#fff;
}
*{margin:0;padding:0;box-sizing:border-box}
html,body{width:802px;height:1200px;overflow:hidden;background:var(--white)}
body{position:relative;font-family:"Open Sans",sans-serif;color:var(--text)}
.abs{position:absolute}

.topline{left:0;top:0;width:802px;height:3px;background:var(--black)}
.brand{left:54px;top:26px;display:flex;align-items:center;gap:7px}
.brand-mark{width:14px;height:14px;background:var(--ink)}
.brand-name{font-family:"Open Sans",sans-serif;font-weight:700;font-size:10px;line-height:13px;color:var(--ink);letter-spacing:.5px;text-transform:uppercase}

.search{left:554px;top:17px;width:174px;height:22px;display:flex}
.search-field{flex:1;border:1px solid var(--line);border-right:0;border-radius:2px 0 0 2px;background:#fafafa;font-size:8.5px;color:#aaa;padding:5px 6px}
.search-go{width:27px;background:var(--black);color:var(--white);font-size:8.5px;font-weight:700;display:flex;align-items:center;justify-content:center;border-radius:0 2px 2px 0}

.nav{top:50px;left:357px;display:flex;align-items:center;height:20px;font-size:9.6px;color:var(--ink)}
.nav a{color:var(--ink);text-decoration:none;margin-right:12px}
.nav a.active{background:linear-gradient(#3a3a3a,#0d0d0d);color:var(--white);padding:0 10px;height:20px;line-height:20px;border-radius:2px;margin-right:12px}
.nav a:last-child{margin-right:0}

.hero{left:0;top:82px;width:802px;height:355px;background:linear-gradient(180deg,#2f7fc9 0%,#79aedb 38%,#9a8a78 62%,#4f5540 82%,#b9b3a8 100%)}
.hero-panel{left:54px;top:191px;width:363px;height:139px;background:rgba(8,12,20,.82);padding:16px 16px 0 16px}
.hero-title{font-family:"Montserrat",sans-serif;font-size:17.5px;color:var(--white);font-weight:400;line-height:22px}
.hero-title b{font-weight:600;margin-right:4px}
.hero-copy{margin-top:9px;font-size:8.6px;line-height:12px;color:#e8e8e8;width:330px}
.hero-btn{margin-top:10px;display:inline-block;background:var(--cream);color:var(--ink);font-size:9.2px;font-weight:600;padding:7px 14px;border-radius:2px}

.welcome{left:0;top:470px;width:802px;text-align:center}
.welcome h1{font-family:"Source Sans 3",sans-serif;font-weight:300;font-size:23px;color:var(--ink);letter-spacing:-.6px}
.welcome h1 b{font-weight:700}
.welcome p{margin:10px auto 0;width:600px;font-size:9.8px;line-height:14.5px;color:#666}

.services{left:0;top:592px;width:802px;height:206px;background:var(--band)}
.card{top:37px;width:126px;height:136px;background:var(--white)}
.card-img{width:126px;height:114px}
.card-cap{font-size:9.5px;color:var(--ink);padding:5px 6px}

.col-title{font-family:"Source Sans 3",sans-serif;font-weight:300;font-size:20px;color:var(--ink);letter-spacing:-.4px}
.about{left:54px;top:828px;width:320px}
.about p{margin-top:11px;font-size:9.4px;line-height:13.4px;color:var(--text)}
.btn-dark{display:inline-block;background:linear-gradient(#3a3a3a,#0d0d0d);color:var(--white);font-size:9.6px;font-weight:600;padding:0 11px;height:24px;line-height:24px;border-radius:2px}
.about .btn-dark{margin-top:14px}

.contact{left:400px;top:828px;width:329px}
.field{position:absolute;border:1px solid var(--line);background:#fafafa;font-size:8.4px;color:#999;padding:5px 7px;border-radius:1px}
.contact .btn-dark{position:absolute;left:-1px;top:141px}

.footer-rule{left:0;top:1022px;width:802px;height:5px;background:var(--black)}
.footer{left:0;top:1027px;width:802px;height:143px;background:var(--footer)}
.fcol{top:18px}
.fcol h4{font-size:9.8px;font-weight:700;color:var(--white);margin-bottom:8px}
.fcol ul{list-style:none;font-size:8.6px;color:#ddd}
.sitemap li{line-height:13.4px}
.links li{line-height:14.8px}
.fcol p{font-size:8.6px;line-height:13.4px;color:#ddd;margin-bottom:6px}
.fsep{top:35px;width:1px;height:77px;background:#444}
.copy{left:0;top:1170px;width:802px;height:30px;background:var(--footer-deep);color:#eee;font-size:8.6px;text-align:center;line-height:30px}
</style>
</head>
<body>

<div class="abs topline"></div>

<header>
  <div class="abs brand">
    <span class="brand-mark"></span>
    <span class="brand-name">Tavron<br>Security Services Ltd</span>
  </div>
  <div class="abs search">
    <div class="search-field">Search</div>
    <div class="search-go">GO</div>
  </div>
  <nav class="abs nav">
    <a class="active" href="#">Home</a>
    <a href="#">About Us</a>
    <a href="#">Security Services</a>
    <a href="#">Why Us</a>
    <a href="#">Testimonials</a>
    <a href="#">Contct Us</a>
  </nav>
</header>

<section class="abs hero" role="img" aria-label="Photo of a dome security camera mounted above a residential street with houses and trees under a blue sky"></section>
<div class="abs hero-panel">
  <h2 class="hero-title"><b>Newzealand’s Best</b> Security Company</h2>
  <p class="hero-copy">It is a long established fact that a reader will be distracted by the readable content of a page when looking at its layout. The point of using Lorem Ipsum is that it has a more-or-less normal distribution of letters</p>
  <span class="hero-btn">READ MORE</span>
</div>

<section class="abs welcome">
  <h1>Welcome to <b>Tavron</b></h1>
  <p>Lorem ipsum dolor sit amet, consectetur adipisicing elit, sed do eiusmod tempor incididunt ut labore et dolore magna aliqua ut enim ad minim veniam, quis nostrud exercitation ullamco laboris nisi ut aliquip ex ea commodo consequat &nbsp;aute irure dolor in reprehenderit in voluptate velit esse cillum dolore eu fugiat nulla pariatur excepteur sint occaecat cupidatat non proident, sunt in culpa.</p>
</section>

<section class="abs services">
  <div class="abs card" style="left:54px">
    <div class="card-img" role="img" aria-label="Photo of a fixed bullet security camera" style="background:linear-gradient(160deg,#e4e6e6,#a9abad)"></div>
    <div class="card-cap">Fixed Camra Systems</div>
  </div>
  <div class="abs card" style="left:190px">
    <div class="card-img" role="img" aria-label="Photo of a dome camera against a blue sky" style="background:linear-gradient(160deg,#2f6fb8,#5a8fcc 60%,#8a9aa8)"></div>
    <div class="card-cap">Camra Systems</div>
  </div>
  <div class="abs card" style="left:327px">
    <div class="card-img" role="img" aria-label="Photo of a guard in a monitoring room with screens" style="background:linear-gradient(160deg,#8b98a6,#3e4a5a 55%,#c08a4a)"></div>
    <div class="card-cap">Guard Services</div>
  </div>
  <div class="abs card" style="left:465px">
    <div class="card-img" role="img" aria-label="Photo of a wall mounted security camera" style="background:linear-gradient(160deg,#c6ccd4,#9aa3ad)"></div>
    <div class="card-cap">Fixed Camra Systems</div>
  </div>
  <div class="abs card" style="left:602px">
    <div class="card-img" role="img" aria-label="Photo of a hand entering a code on an alarm keypad" style="background:linear-gradient(160deg,#f2f2f2,#cfd2d4 60%,#d9b7a0)"></div>
    <div class="card-cap">Alarm System</div>
  </div>
</section>

<section class="abs about">
  <h2 class="col-title">About Us</h2>
  <p>Lorem ipsum dolor sit amet, consectetur adipisicing elit, sed do eiusmod tempor incididunt ut labore et dolore magna aliqua enim minim veniam quis nostrud exercitation ullamco laboris nisi ut aliquip ex ea commodo consequat &nbsp;aute irure dolor reprehenderit in voluptate velit cillum dolore eu fugiat nulla pariatur excepteur sint occaecat cupidatat proident sunt qui officia deserunt mollit anim id est laborum.</p>
  <span class="btn-dark">Read More</span>
</section>

<section class="abs contact">
  <h2 class="col-title">Contact Us</h2>
  <div class="field" style="left:0;top:38px;width:163px;height:23px">Name</div>
  <div class="field" style="left:166px;top:38px;width:163px;height:23px">Email Address</div>
  <div class="field" style="left:0;top:65px;width:329px;height:67px">Message</div>
  <span class="btn-dark">Read More</span>
</section>

<div class="abs footer-rule"></div>
<footer class="abs footer">
  <div class="abs fcol sitemap" style="left:74px">
    <h4>Site Map</h4>
    <ul>
      <li style="color:#fff;font-weight:600">Home</li>
      <li>About Us</li>
      <li>Security Services</li>
      <li>Why Us</li>
      <li>Testimonials</li>
      <li>Contct Us</li>
    </ul>
  </div>
  <div class="abs fsep" style="left:176px"></div>
  <div class="abs fcol links" style="left:210px">
    <h4>Links</h4>
    <ul>
      <li>Lorem ipsum dolor sit</li>
      <li>Ame cnsectetur adipisicing</li>
      <li>Elit sed &nbsp;eiusmod tempor</li>
      <li>Incididunt ut labore et</li>
      <li>Dolore magna</li>
    </ul>
  </div>
  <div class="abs fsep" style="left:347px"></div>
  <div class="abs fcol links" style="left:386px">
    <h4>Our Services</h4>
    <ul>
      <li>Ullamco laboris nisi ut</li>
      <li>Aliquip ex ea commodo</li>
      <li>Consequat &nbsp;aute irure</li>
      <li>Dolor reprehenderit</li>
    </ul>
  </div>
  <div class="abs fsep" style="left:514px"></div>
  <div class="abs fcol" style="left:550px;width:170px">
    <h4>Contact Us</h4>
    <p>Lorem ipsum dolor sit amet, consectetur adipisicing elit.</p>
    <p>Call: 123 465 7890</p>
    <p>Email: info@tavronsecurity.co.nz</p>
  </div>
</footer>
<div class="abs copy">Copy rigthe 2014 © Tavron. All rights reserved</div>

</body>
</html>
```